Postcard for our major fundraising event - KindlingJOY2018

Bright Harbor KIDS Camp (BHK) and Youth Summit Trail Camp (YSTC) are ministries of Lindell Fellowship Church that serve Ventura County children of abuse, abandonment and neglect living in foster care. We are looking for a postcard design to promote our single largest fundraising event of the year, GatheringJOY2018, to raise awareness and support for children of abuse. GatheringJOY is a dinner banquet on at an exclusive outdoor venue, "Willow Hollow" with a rustic, ranch feel and with spectacular panoramic views of the City of Camarillo. The event will include music, refreshments, appetizers, a Santa Maria-style barbeque (BBQ), coffee and dessert, testimonials from camp, prize drawings, an opportunity to partner with BHK and YSTC, and time to socialize before and after.
Updates

I have just uploaded text copy to help designers come closer to what we are looking for. Thank you very much for your interest! -Rob

Target Market(s)

People from both within and from outside our sponsoring church who have a heart for hurting children and who are willing and able to financially support our camping (BHK & YSTC) ministries.

Industry/Entity Type

Church

Font styles to use
Serif
Decorative
Script

Requirements
Must have
• Name: GatheringJOY2018... raising awareness and support for children of abuse
• Date: Thursday, May 24, 2018, 6:30-8:00 pm
• Place: Willow Hollow at Dunmore Ranch, 2715 Barlow Lane, Somis, California.
• Cost: $30 per person
• Tickets: Available at Tixlane.com
• Front side should include the elements of the event (although not necessarily bulleted like below):
• • Social hour
• • Music
• • Hors d’eourves
• • Refreshments
• • Santa Maria-style BBQ dinner
• • Coffee & dessert
• • Prize drawings
• • Stories from camp
• See attachment for suggested copy for back side.
• BHK and YSTC logos should be included on the postcard. I’ve uploaded a variety of photos for the designer to choose from; they do not necessarily all have to be included. There are also lots more pics available on our Facebook (Bright Harbor KIDS of Ventura).
• The front-side of the postcard can be entirely images and text. The back-side of the post card should include our return address at the top left ("BHK/YSTC of Lindell Fellowship Church, 418 Kestrel Ridge Way, Ventura, CA 93017") and should leave at least the right half of the postcard clear for addressing and postage.
• BHK colors are purple (Pantone 267) and red (Pantone 186). YSTC colors are green and yellow.
Nice to have
• A selection of camp photos large enough to easily view, but no so many that they are too small to identify. And, perhaps, a design element that evokes a rustic, outdoors, western, ranch feel, but not so much that it seems that we are promoting a country hoedown.
Should not have
• Anything sexual or sensual, related to alcoholic beverages, gambling, guns, or anything negative.

```html
<!DOCTYPE html>
<html lang="en">
<head>
<meta charset="utf-8">
<title>GatheringJOY 2018 Postcard</title>
<link rel="stylesheet" href="https://fonts.googleapis.com/css2?family=Montserrat:ital,wght@0,400;0,500;0,600;0,700;1,400;1,500&family=Mrs+Saint+Delafield&display=swap">
<style>
:root{
  --red:#d01f2e;
  --purple:#2f2566;
  --white:#ffffff;
  --ink:#222;
  --rule:#bdbdbd;
  --stage:#ececec;
  --stamp:#dcdcdc;
  --green:#3a8f3e;
  --yellow:#f2c21b;
  --pink:#e98a93;
}
*{box-sizing:border-box;margin:0;padding:0}
html,body{width:1200px;height:903px;overflow:hidden}
body{background:var(--stage);position:relative;font-family:"Montserrat",sans-serif;color:var(--ink)}
.card{position:absolute;width:581px;height:377px;background:var(--white);overflow:hidden;box-shadow:0 4px 14px rgba(0,0,0,.18)}
.card--front{left:115px;top:66px}
.card--back{left:504px;top:477px}
.card svg.base{position:absolute;inset:0}
.activities{position:absolute;inset:0;color:var(--white);font-size:12px;letter-spacing:.2px}
.activities span{position:absolute;white-space:nowrap;line-height:15px}
.back-text{position:absolute;left:0;top:0;width:300px;height:308px}
.logo{position:absolute;top:26px;display:flex;align-items:center;gap:5px;font-weight:700;font-size:11px;color:var(--purple);white-space:nowrap}
.logo i{display:inline-block;width:14px;height:14px;border-radius:50%}
.logo--bhk{left:38px}
.logo--bhk i{background:var(--red)}
.logo--ystc{left:182px;color:var(--green)}
.logo--ystc i{background:var(--yellow)}
.line{position:absolute;left:0;width:300px;text-align:center;white-space:nowrap;line-height:1.2}
.hosts{top:62px;font-size:8.5px}
.hosts-sub{top:72px;font-size:8.5px}
.invite{top:86px;font-size:8px;font-style:italic;font-weight:500}
.event-name{top:100px;width:297px;font-size:22px;font-weight:700;color:var(--white);letter-spacing:.3px}
.tagline{top:130px;font-family:"Mrs Saint Delafield",cursive;font-size:17px;line-height:20px}
.exclusive{top:152px;font-size:9.5px;font-style:italic;color:var(--red)}
.venue{font-size:12px;color:var(--purple);letter-spacing:.3px}
.venue--a{top:166px}
.venue--b{top:179px}
.date{top:197px;left:57px;width:182px;height:20px;line-height:20px;background:var(--red);color:var(--white);font-size:15px;border-radius:4px;letter-spacing:.3px}
.time{top:220px;font-size:14px;color:var(--purple)}
.tickets-label{position:absolute;left:60px;top:239px;font-size:10.5px;line-height:13px;font-weight:700;color:var(--red);letter-spacing:.5px;background:var(--white);padding:0 3px;z-index:2}
.ticket-box{position:absolute;left:15px;top:247px;width:147px;height:27px;border:1px solid #888;border-radius:4px;font-size:17px;color:var(--purple);line-height:25px;text-align:center;white-space:nowrap}
.ticket-box b{color:var(--red)}
.availability{position:absolute;left:170px;top:246px;font-size:12px;text-align:left;line-height:14px;white-space:nowrap}
.availability span{color:var(--red)}
.proceeds{top:280px;width:280px;font-size:9px}
.proceeds-sub{top:291px;width:280px;font-size:9px;color:var(--red)}
.contacts{position:absolute;left:0;top:308px;width:272px;height:69px;color:var(--white);font-size:7px}
.contacts h3{position:absolute;top:5px;width:100%;text-align:center;font-size:7.5px;font-weight:600;line-height:10px}
.contact{position:absolute;top:18px;line-height:10px;white-space:nowrap}
.contact--bhk{left:18px}
.contact--ystc{left:149px}
.contact .role{color:var(--pink)}
.contact b{font-weight:600}
.contact .ico{display:inline-block;width:5px;height:5px;border-radius:1px;background:var(--pink);margin-right:3px;vertical-align:middle}
.return-address{position:absolute;left:325px;top:42px;font-size:8.5px;line-height:10.5px;font-style:normal}
.stamp{position:absolute;left:502px;top:27px;width:57px;height:66px;background:var(--stamp)}
.address-line{position:absolute;left:317px;width:243px;height:1px;background:var(--rule)}
</style>
</head>
<body>

<section class="card card--front" aria-label="Postcard front">
  <svg class="base" width="581" height="377" viewBox="0 0 581 377">
    <path role="img" aria-label="Photo: children riding horses along a shaded camp trail" d="M0 0H581V146Q400 118 260 150Q120 180 0 140Z" fill="#4b5a34"/>
    <path role="img" aria-label="Photo: camp dinner with volunteers serving children at tables" d="M0 146Q100 178 190 165V286Q100 270 0 286Z" fill="#7c8a48"/>
    <path role="img" aria-label="Photo: two girls in pink sun hats smiling at a table" d="M196 164Q280 152 385 147V276Q290 272 196 284Z" fill="#b06d84"/>
    <path role="img" aria-label="Photo: boys practicing archery on a grassy field" d="M391 146Q490 134 581 120V284Q490 274 391 276Z" fill="#5f7d3c"/>
    <path d="M0 290Q150 270 290 278Q430 284 581 297V377H0Z" fill="var(--red)"/>
    <rect x="0" y="361" width="581" height="16" fill="var(--purple)"/>
  </svg>
  <div class="activities">
    <span style="left:30px;top:306px">Social hour</span>
    <span style="left:128px;top:306px">Hors d’eourves</span>
    <span style="left:249px;top:306px">Santa Maria-style BBQ dinner</span>
    <span style="left:451px;top:306px">Prize drawings</span>
    <span style="left:30px;top:333px">Music</span>
    <span style="left:128px;top:333px">Refreshments</span>
    <span style="left:249px;top:333px">Coffee &amp; dessert</span>
    <span style="left:451px;top:333px">Stories from camp</span>
  </div>
</section>

<section class="card card--back" aria-label="Postcard back">
  <svg class="base" width="582" height="377" viewBox="0 0 582 377">
    <path d="M0 99H297L291 129H0Z" fill="var(--red)"/>
    <path d="M0 308H274L270 377H0Z" fill="var(--purple)"/>
    <line x1="301" y1="0" x2="270" y2="377" stroke="var(--purple)" stroke-width="2.5"/>
  </svg>

  <div class="back-text">
    <div class="logo logo--bhk"><i></i>Bright Harbor KIDS</div>
    <div class="logo logo--ystc"><i></i>YSTC</div>
    <p class="line hosts">Bright Harbor KIDS Camp &amp; Youth Summit Trail Camp</p>
    <p class="line hosts-sub">of Lindell Fellowship Church</p>
    <p class="line invite">invite you to join us for</p>
    <h1 class="line event-name">GatheringJOY 2018</h1>
    <p class="line tagline">raising awareness and support for children of abuse</p>
    <p class="line exclusive">at the exclusive</p>
    <p class="line venue venue--a">Willow Hollow at Dunmore Ranch</p>
    <p class="line venue venue--b">2715 Barlow Lane, Somis, CA</p>
    <p class="line date">Thursday, May 24, 2018</p>
    <p class="line time">6:30-8:00 pm</p>
    <span class="tickets-label">TICKETS:</span>
    <div class="ticket-box"><b>$30</b> per person</div>
    <p class="availability">Available at<br><span>Tixlane.com</span></p>
    <p class="line proceeds">All proceeds to benefit</p>
    <p class="line proceeds-sub">BHKC &amp; YSTC serving children of abuse ages 7-14.</p>
  </div>

  <div class="contacts">
    <h3>For more information:</h3>
    <div class="contact contact--bhk">
      <div class="role">BHKC:</div>
      <div><b>Rob Halvorsen</b> ( Director )</div>
      <div><span class="ico"></span>(805) 555-0142</div>
      <div><span class="ico"></span>bhkcventura@northmail.net</div>
    </div>
    <div class="contact contact--ystc">
      <div class="role">YSTC:</div>
      <div><b>Dana Whitcomb</b> ( Director )</div>
      <div><span class="ico"></span>(805) 555-0187</div>
      <div><span class="ico"></span>dwhitcomb@inboxly.com</div>
    </div>
  </div>

  <address class="return-address">
    BHK/YSTC of<br>Lindell Fellowship Church,<br>418 Kestrel Ridge Way,<br>Ventura, CA 93017
  </address>
  <div class="stamp"></div>
  <div class="address-line" style="top:176px"></div>
  <div class="address-line" style="top:214px"></div>
  <div class="address-line" style="top:246px"></div>
</section>

</body>
</html>
```